Brivolt Technologies business card design

We need a business card designed with our new logo. it would be great if the card could communicate it is a technology based company.

Target Market(s)

system integrators

Industry/Entity Type

technology, IOT

Contact Information for Business Card

Name, designation, Address, telephone number, email address

Requirements
Must have
• logo and company name
Nice to have
• something to do with technology

```html
<!DOCTYPE html>
<html lang="en">
<head>
<meta charset="utf-8">
<title>Brivolt Technologies business card</title>
<link href="https://fonts.googleapis.com/css2?family=Open+Sans:wght@400;700&display=swap" rel="stylesheet">
<style>
  :root {
    --backdrop: #3b3b3b;
    --card: #1b1b1b;
    --accent: #f2941e;
    --ink: #f2f2f2;
    --muted: #d8d8d8;
  }
  html, body {
    margin: 0;
    padding: 0;
    width: 1200px;
    height: 801px;
    overflow: hidden;
    background: var(--backdrop);
    font-family: "Open Sans", Arial, sans-serif;
  }
  .stage {
    position: relative;
    width: 1200px;
    height: 801px;
  }
  .card {
    position: absolute;
    top: 250px;
    width: 520px;
    height: 300px;
    background: var(--card);
    box-shadow: 0 3px 0 var(--accent), 0 18px 40px rgba(0,0,0,.45);
    overflow: hidden;
  }
  .card--front { left: 40px; }
  .card--back { left: 640px; }

  .brand {
    position: absolute;
    display: flex;
    align-items: center;
    gap: 10px;
    color: var(--ink);
    font-weight: 700;
    letter-spacing: 1px;
  }
  .brand__mark {
    width: 14px;
    height: 14px;
    background: var(--accent);
    flex: none;
  }
  .card--front .brand {
    left: 32px;
    top: 96px;
    font-size: 20px;
  }

  .person {
    position: absolute;
    right: 32px;
    top: 44px;
    text-align: right;
  }
  .person__name {
    margin: 0;
    color: var(--accent);
    font-weight: 700;
    font-size: 20px;
    letter-spacing: .5px;
  }
  .person__role {
    margin: 2px 0 0;
    color: var(--ink);
    font-size: 13px;
  }

  .divider {
    position: absolute;
    left: 150px;
    right: 0;
    top: 162px;
    height: 1px;
    background: var(--accent);
  }

  .contacts {
    position: absolute;
    left: 150px;
    top: 186px;
    margin: 0;
    padding: 0;
    list-style: none;
    color: var(--muted);
    font-size: 13px;
    line-height: 22px;
  }
  .contacts li {
    display: flex;
    align-items: center;
    gap: 8px;
  }
  .contacts svg { width: 11px; height: 11px; fill: var(--accent); flex: none; }

  .address {
    position: absolute;
    right: 32px;
    top: 186px;
    margin: 0;
    text-align: right;
    color: var(--ink);
    font-size: 13px;
    line-height: 20px;
    font-style: normal;
  }

  .card--back .brand {
    right: 36px;
    bottom: 70px;
    font-size: 30px;
    letter-spacing: 2px;
  }
  .card--back .brand__mark { width: 20px; height: 20px; }
</style>
</head>
<body>
<main class="stage">

  <section class="card card--front" aria-label="Card front">
    <div class="brand"><span class="brand__mark"></span>BRIVOLT TECHNOLOGIES</div>

    <div class="person">
      <p class="person__name">DARA KELLMONT</p>
      <p class="person__role">President</p>
    </div>

    <div class="divider"></div>

    <ul class="contacts">
      <li>
        <svg viewBox="0 0 24 24" aria-hidden="true"><path d="M6.6 10.8a15 15 0 0 0 6.6 6.6l2.2-2.2a1 1 0 0 1 1-.25 11.4 11.4 0 0 0 3.6.57 1 1 0 0 1 1 1V20a1 1 0 0 1-1 1A17 17 0 0 1 3 4a1 1 0 0 1 1-1h3.5a1 1 0 0 1 1 1c0 1.25.2 2.45.57 3.57a1 1 0 0 1-.25 1z"/></svg>
        555-310-4827
      </li>
      <li>
        <svg viewBox="0 0 24 24" aria-hidden="true"><path d="M2 5h20v14H2z M4 7v.5l8 5 8-5V7l-8 5z" fill-rule="evenodd"/></svg>
        info@brivolttechnologies.com
      </li>
      <li>
        <svg viewBox="0 0 24 24" aria-hidden="true"><circle cx="12" cy="12" r="10"/></svg>
        www.brivolttechnologies.com
      </li>
    </ul>

    <address class="address">18420 Coral Bay Drive<br>Seacliff CA 90417</address>
  </section>

  <section class="card card--back" aria-label="Card back">
    <div class="brand"><span class="brand__mark"></span>BRIVOLT TECHNOLOGIES</div>
  </section>

</main>
</body>
</html>
```